Brookvale Estates LLC stationary for a real estate property management company.

Create stationary (letterhead, envelopes, business cards) using Brookvale Estates LLC logo as primary creative element. Stationary design needs to be horizontal, leaving as much space as possible for correspondence copy. See attached Creative Brief and past stationary files for details.

Target Market(s)

Prospective apartment residents and current residents, vendors, and government agencies.

Industry/Entity Type

Property Management

Contact Information for Business Card

Business card employee title: Property Manager. Should include address, phone, fax, email, website, slogan, and Brookvale Estates logo.

Font styles to use
Sans Serif

Colors
0592cd
000000

Requirements
Must have
• Tone should be conservative, institutional, business (i.e. banking, finance, real estate). Must include: address, phone, fax, website, and slogan (see attached Creative Brief). Should be a horizontal design, leaving as much room as possible for letter correspondence copy.
Nice to have
• Please use an Arial or Helvetica style font.
Should not have
• Letterhead layout should leave as much room as possible for copy.

```html
<!DOCTYPE html>
<html lang="en">
<head>
<meta charset="utf-8">
<title>Brookvale Estates LLC – Business Card</title>
<link rel="stylesheet" href="https://fonts.googleapis.com/css2?family=Arimo:wght@400;700&display=swap">
<style>
  :root {
    --brand-blue: #10669f;
    --ink-grey: #444547;
    --text-grey: #4a4b4d;
    --card-white: #f4f4f4;
    --back-light: #6c6d70;
    --back-dark: #3d3e41;
    --stage: #7a5b45;
  }
  * { margin: 0; padding: 0; box-sizing: border-box; }
  html, body {
    width: 1200px;
    height: 960px;
    overflow: hidden;
    background: var(--stage);
    font-family: "Arimo", Arial, Helvetica, sans-serif;
  }
  .canvas {
    position: relative;
    width: 1200px;
    height: 960px;
  }
  .card {
    position: absolute;
    width: 600px;
    height: 340px;
    box-shadow: 0 2px 6px rgba(0,0,0,0.35);
  }
  .card-front {
    left: 302px;
    top: 130px;
    background: var(--card-white);
    overflow: hidden;
  }
  .card-front .side-band {
    position: absolute;
    left: 0; top: 0;
    width: 100px;
    height: 100%;
    background: var(--brand-blue);
  }
  .card-front .details {
    position: absolute;
    right: 27px;
    top: 38px;
    text-align: right;
    color: var(--text-grey);
  }
  .company-name {
    color: var(--brand-blue);
    font-weight: 700;
    font-size: 27px;
    letter-spacing: 0.5px;
    text-transform: uppercase;
    line-height: 1.1;
  }
  .person-name {
    margin-top: 42px;
    color: var(--brand-blue);
    font-weight: 700;
    font-size: 19px;
    text-transform: uppercase;
  }
  .person-title {
    margin-top: 4px;
    font-size: 16px;
  }
  .address {
    margin-top: 12px;
    font-size: 14px;
    line-height: 19px;
  }
  .contact {
    margin-top: 10px;
    font-size: 14px;
    line-height: 19px;
  }
  .slogan {
    margin-top: 10px;
    color: var(--brand-blue);
    font-weight: 700;
    font-size: 14px;
  }
  .card-back {
    left: 299px;
    top: 490px;
    background: linear-gradient(135deg, var(--back-light) 0%, var(--back-dark) 55%, var(--back-dark) 100%);
    display: flex;
    align-items: center;
    justify-content: center;
    gap: 16px;
  }
  .brand-dot {
    width: 26px;
    height: 26px;
    border-radius: 50%;
    background: var(--brand-blue);
  }
  .back-name {
    color: #ffffff;
    font-weight: 700;
    font-size: 30px;
    letter-spacing: 1px;
    text-transform: uppercase;
  }
</style>
</head>
<body>
  <main class="canvas">
    <section class="card card-front">
      <div class="side-band"></div>
      <div class="details">
        <h1 class="company-name">Brookvale Estates LLC</h1>
        <p class="person-name">Daniel Hartley</p>
        <p class="person-title">Property Manager</p>
        <p class="address">2780 Alder Ridge Road #B210<br>Fairview, CA 92140</p>
        <p class="contact">
          Phone: 555-014-2273<br>
          Fax: 555-019-6604<br>
          daniel@brookvaleestates.us<br>
          www.brookvaleestates.us
        </p>
        <p class="slogan">Multifamily Property Management</p>
      </div>
    </section>
    <section class="card card-back">
      <span class="brand-dot"></span>
      <span class="back-name">Brookvale Estates LLC</span>
    </section>
  </main>
</body>
</html>
```